Corvelle Meadow Organic Flower Farm, Farmer Florist

I am a flower grower and florist, so I do everything from the field to the vase. I want to include my website, phone, email and instagram

```html
<!DOCTYPE html>
<html lang="en">
<head>
<meta charset="utf-8">
<title>Corvelle Meadow – Business Card</title>
<link rel="stylesheet" href="https://fonts.googleapis.com/css2?family=Playfair+Display:wght@400&family=Inter:wght@400&family=Montserrat:wght@400;500&display=swap">
<style>
  :root {
    --paper: #ffffff;
    --blush: #f38f92;
    --plum: #5a2e33;
    --ink: #2b1a1c;
    --cream: #ffffff;
  }
  html, body {
    margin: 0;
    padding: 0;
    overflow: hidden;
    background: var(--paper);
  }
  .card {
    position: relative;
    width: 1200px;
    height: 686px;
    background: var(--paper);
    overflow: hidden;
  }
  .brand {
    position: absolute;
    left: 0;
    top: 0;
    width: 670px;
    height: 686px;
    display: flex;
    flex-direction: column;
    align-items: center;
    justify-content: center;
  }
  .brand-dot {
    width: 34px;
    height: 34px;
    border-radius: 50%;
    background: var(--blush);
    margin-bottom: 26px;
  }
  .brand-name {
    margin: 0;
    font-family: "Playfair Display", serif;
    font-weight: 400;
    font-size: 64px;
    letter-spacing: 7px;
    color: var(--plum);
    line-height: 1;
  }
  .brand-tagline {
    margin: 22px 0 0;
    font-family: "Playfair Display", serif;
    font-size: 24px;
    letter-spacing: 3px;
    color: var(--blush);
    line-height: 1;
  }
  .brand-established {
    margin: 20px 0 0;
    font-family: "Playfair Display", serif;
    font-size: 20px;
    letter-spacing: 5px;
    color: var(--plum);
    line-height: 1;
  }
  .details {
    position: absolute;
    left: 670px;
    top: 0;
    width: 530px;
    height: 686px;
    background: var(--blush);
  }
  .person-name {
    position: absolute;
    left: 80px;
    top: 100px;
    margin: 0;
    font-family: "Playfair Display", serif;
    font-weight: 400;
    font-size: 60px;
    letter-spacing: 2px;
    color: var(--cream);
    line-height: 1;
    text-transform: uppercase;
  }
  .person-role {
    position: absolute;
    left: 80px;
    top: 184px;
    margin: 0;
    font-family: "Inter", sans-serif;
    font-size: 19px;
    color: var(--cream);
    text-transform: uppercase;
  }
  .contact-list {
    position: absolute;
    left: 81px;
    top: 256px;
    margin: 0;
    padding: 0;
    list-style: none;
  }
  .contact-item {
    display: flex;
    align-items: center;
    height: 60px;
    margin-bottom: 32px;
  }
  .contact-icon {
    width: 60px;
    height: 60px;
    border-radius: 50%;
    background: var(--plum);
    display: flex;
    align-items: center;
    justify-content: center;
    flex-shrink: 0;
  }
  .contact-icon svg {
    width: 28px;
    height: 28px;
  }
  .contact-icon-at {
    font-family: "Montserrat", sans-serif;
    font-weight: 500;
    font-size: 30px;
    line-height: 1;
    color: var(--cream);
    margin-top: -3px;
  }
  .contact-text {
    margin-left: 20px;
    font-family: "Montserrat", sans-serif;
    font-size: 21px;
    color: var(--ink);
  }
</style>
</head>
<body>
  <main class="card">
    <section class="brand" aria-label="Corvelle Meadow">
      <div class="brand-dot"></div>
      <h1 class="brand-name">CORVELLE</h1>
      <p class="brand-tagline">organic flower farm</p>
      <p class="brand-established">EST. 2019</p>
    </section>

    <section class="details">
      <h2 class="person-name">Maren Holt</h2>
      <p class="person-role">Farmer Florist</p>

      <ul class="contact-list">
        <li class="contact-item">
          <span class="contact-icon" aria-hidden="true">
            <svg viewBox="0 0 24 24"><path fill="#fff" d="M6.6 10.8a15.1 15.1 0 0 0 6.6 6.6l2.2-2.2a1 1 0 0 1 1-.25 11.4 11.4 0 0 0 3.6.57 1 1 0 0 1 1 1V20a1 1 0 0 1-1 1A17 17 0 0 1 3 4a1 1 0 0 1 1-1h3.5a1 1 0 0 1 1 1c0 1.250.2 2.45.57 3.57a1 1 0 0 1-.25 1z"/></svg>
          </span>
          <span class="contact-text">(708) 5550 1827</span>
        </li>
        <li class="contact-item">
          <span class="contact-icon" aria-hidden="true">
            <svg viewBox="0 0 24 24"><rect x="2" y="5" width="20" height="14" rx="1.5" fill="#fff"/><path d="M2.5 6l9.5 7 9.5-7" fill="none" stroke="#5a2e33" stroke-width="1.6"/></svg>
          </span>
          <span class="contact-text">hello@corvellemeadow.com.au</span>
        </li>
        <li class="contact-item">
          <span class="contact-icon" aria-hidden="true">
            <svg viewBox="0 0 24 24" fill="none" stroke="#fff" stroke-width="1.8"><circle cx="12" cy="12" r="9"/><ellipse cx="12" cy="12" rx="4" ry="9"/><path d="M3 12h18M4.5 7.5h15M4.5 16.5h15"/></svg>
          </span>
          <span class="contact-text">www.corvellemeadow.com</span>
        </li>
        <li class="contact-item">
          <span class="contact-icon" aria-hidden="true"><span class="contact-icon-at">@</span></span>
          <span class="contact-text">corvellemeadowoninstagram</span>
        </li>
      </ul>
    </section>
  </main>
</body>
</html>
```